Building company buisness cards

We are looking for a sharp modern new look for our business cards.
We are a New Zealand based company that specialises in house and land packages.
We have attached a photo of the current logo and would like to see if it can be improved somehow if needed.
We are open to any colours but we have chosen green at this stage.
Feel free to change the font and make the logo smarter looking.
Play with the colours and see what looks best.

We want a card that looks so good know one will want to throw it away!

Target Market(s)

Home buyers

Industry/Entity Type

Building

Contact Information for Business Card

Derek Tolvane
0217394062
dtolvane@quillmarkhomesteads.co.nz
quillmarkhomesteads.co.nz

Font styles to use
Serif
Sans Serif

Colors

Designer to choose colors to be used in the design.

Requirements
Must have
• Logo and company name on one side, details on the other side
Nice to have
• Color codes for the original green are HEX #4a8028, RGB(74,128,40), CMYK(42,0,69,50)
• Round corners, Raised and/or spot UV

```html
<!DOCTYPE html>
<html lang="en">
<head>
<meta charset="utf-8">
<title>Quillmark Homesteads — Business Card</title>
<link rel="stylesheet" href="https://fonts.googleapis.com/css2?family=Montserrat:wght@600;800&family=Open+Sans:wght@400;600&display=swap">
<style>
  :root {
    --brand-green: #4a7a36;
    --brand-green-deep: #3b6529;
    --brand-green-light: #5a8c44;
    --card-white: #f7f7f6;
    --card-white-edge: #ebebe9;
    --motif-grey: #e2e5df;
    --ink: #1f1f1f;
    --backdrop: #e9e6e1;
  }
  * { margin: 0; padding: 0; box-sizing: border-box; }
  html, body { width: 1200px; height: 1021px; overflow: hidden; }
  body {
    background: var(--backdrop);
    position: relative;
    font-family: "Open Sans", Arial, sans-serif;
  }
  .card {
    position: absolute;
    left: 220px;
    width: 760px;
    height: 434px;
    border-radius: 26px;
    overflow: hidden;
    box-shadow: 0 6px 18px rgba(0,0,0,0.18);
  }
  .card--back { top: 40px; background: var(--brand-green); }
  .card--front {
    top: 547px;
    background: linear-gradient(135deg, #fdfdfc 0%, var(--card-white) 55%, var(--card-white-edge) 100%);
  }

  /* Back: tonal embossed pattern area */
  .pattern-area {
    position: absolute; inset: 0;
    background:
      radial-gradient(ellipse at 35% 30%, rgba(255,255,255,0.10) 0%, rgba(255,255,255,0) 55%),
      linear-gradient(125deg, var(--brand-green-light) 0%, var(--brand-green) 50%, var(--brand-green-deep) 100%);
  }
  .back-lockup {
    position: absolute; inset: 0;
    display: flex; align-items: center; justify-content: center; gap: 18px;
  }
  .brand-dot {
    width: 64px; height: 64px; border-radius: 50%; flex: none;
  }
  .card--back .brand-dot { background: #ffffff; }

  .wordmark {
    font-family: "Montserrat", Arial, sans-serif;
    font-weight: 800;
    line-height: 1;
    letter-spacing: 0.5px;
  }
  .wordmark__main { display: block; font-size: 50px; }
  .wordmark__sub { display: block; font-size: 27px; margin-top: 6px; padding-left: 3px; }
  .card--back .wordmark { color: #ffffff; }

  /* Front */
  .motif-area {
    position: absolute; left: 0; top: 0; width: 330px; height: 434px;
    background: linear-gradient(160deg, var(--motif-grey) 0%, rgba(226,229,223,0.25) 100%);
    opacity: 0.75;
  }
  .contact-block { position: absolute; left: 62px; top: 140px; }
  .contact-block__name {
    font-family: "Montserrat", Arial, sans-serif;
    font-weight: 600; font-size: 28px; color: var(--brand-green); line-height: 1.1;
  }
  .contact-block__role { font-size: 18px; color: var(--ink); margin-bottom: 40px; }
  .contact-list { list-style: none; }
  .contact-list li {
    display: flex; align-items: center; gap: 8px;
    font-size: 18px; color: var(--ink); line-height: 1.35;
  }
  .contact-list svg { width: 15px; height: 15px; flex: none; }

  .front-lockup {
    position: absolute; left: 470px; top: 110px; width: 260px;
    display: flex; flex-direction: column; align-items: center;
  }
  .card--front .brand-dot { background: var(--brand-green); width: 58px; height: 58px; margin-bottom: 16px; }
  .card--front .wordmark { color: var(--brand-green); }
  .card--front .wordmark__main { font-size: 46px; }
  .card--front .wordmark__sub { font-size: 25px; }
</style>
</head>
<body>
  <section class="card card--back" aria-label="Card back">
    <div class="pattern-area" role="img" aria-label="Embossed repeating brand pattern in tonal greens"></div>
    <div class="back-lockup">
      <span class="brand-dot" aria-hidden="true"></span>
      <div class="wordmark">
        <span class="wordmark__main">quillmark</span>
        <span class="wordmark__sub">homesteads.</span>
      </div>
    </div>
  </section>

  <section class="card card--front" aria-label="Card front">
    <div class="motif-area" role="img" aria-label="Faint large brand emblem decoration"></div>
    <div class="contact-block">
      <p class="contact-block__name">Derek Tolvane</p>
      <p class="contact-block__role">Founder</p>
      <ul class="contact-list">
        <li>
          <svg viewBox="0 0 16 16"><path fill="#4a7a36" d="M3.5 1.5l2.5 0 1 3.5-1.7 1.2c.8 1.8 2.2 3.2 4 4l1.2-1.7 3.5 1v2.5c0 .8-.7 1.5-1.5 1.5C6.8 13.5 2 8.7 2 3c0-.8.7-1.5 1.5-1.5z"/></svg>
          0217394062
        </li>
        <li>
          <svg viewBox="0 0 16 16"><rect x="1.5" y="3.5" width="13" height="9" fill="none" stroke="#4a7a36" stroke-width="1.4"/><path d="M1.5 3.5l6.5 5 6.5-5" fill="none" stroke="#4a7a36" stroke-width="1.4"/></svg>
          dtolvane@quillmarkhomesteads.co.nz
        </li>
        <li>
          <svg viewBox="0 0 16 16"><circle cx="8" cy="8" r="6.3" fill="none" stroke="#4a7a36" stroke-width="1.3"/><ellipse cx="8" cy="8" rx="2.8" ry="6.3" fill="none" stroke="#4a7a36" stroke-width="1.1"/><path d="M1.7 8h12.6" stroke="#4a7a36" stroke-width="1.1"/></svg>
          quillmarkhomesteads.co.nz
        </li>
      </ul>
    </div>
    <div class="front-lockup">
      <span class="brand-dot" aria-hidden="true"></span>
      <div class="wordmark">
        <span class="wordmark__main">quillmark</span>
        <span class="wordmark__sub">homesteads.</span>
      </div>
    </div>
  </section>
</body>
</html>
```